Brindle Haven Website design in word press

Develop great looking website home page with basic menus in Word Press. We already have a logo, so no need to re-invent that.

Target Market(s)

donors, animal owners, emergency services.

Number of Pages Required

1 page

Font styles to use
Sans Serif

Colors
ec1f27
000000
ffffff
959595

Requirements
Must have
• Fresh design in Word Press, neutral (i.e. not American looking), uses red, black and white as core colours. Needs to have menu options for about us, join us, help us, FAQs, contact us etc. Looking for a smart, modern, professional looking home page, that we can easily add pages/menu's/widgets to. Include social media buttons for facebook, twitter etc.
Nice to have
• Images (could be in colour shades) of animals in disaster i.e. search royalty free Hurricane Lorimel, Hurrican Odwin.
Should not have
• Images that breach copyright.

```html
<!DOCTYPE html>
<html lang="en">
<head>
<meta charset="utf-8">
<title>Brindle Haven New Zealand</title>
<link rel="stylesheet" href="https://fonts.googleapis.com/css2?family=Roboto:wght@400;500;700;900&family=Poppins:wght@400;500;600&display=swap">
<style>
:root{
  --red:#ec1f27;
  --red-dark:#a8141a;
  --black:#000000;
  --ink:#1b1b1b;
  --white:#ffffff;
  --grey:#959595;
  --light:#ececec;
  --navy:#1f3a6b;
}
*{box-sizing:border-box;margin:0;padding:0}
html,body{width:1200px;height:3766px;overflow:hidden}
body{position:relative;background:var(--white);font-family:"Poppins",sans-serif;color:var(--ink)}
.abs{position:absolute}

/* header */
.site-header{position:absolute;left:0;top:0;width:1200px;height:120px;background:var(--white)}
.brand{position:absolute;left:133px;top:22px;display:flex;align-items:center;gap:12px}
.brand-dot{width:64px;height:64px;border-radius:50%;background:var(--red)}
.brand-name{font-family:"Roboto",sans-serif;font-weight:700;font-size:20px;color:var(--red)}
.callus{position:absolute;left:688px;top:18px;display:flex;align-items:center;gap:10px}
.callus small{display:block;font-size:13px;color:var(--ink)}
.callus strong{display:block;font-family:"Roboto",sans-serif;font-size:24px;color:var(--red);line-height:1}
.btn-donate-top{position:absolute;left:903px;top:22px;width:163px;height:40px;border-radius:20px;background:var(--red);color:var(--white);font-family:"Roboto",sans-serif;font-weight:700;font-size:15px;display:flex;align-items:center;justify-content:center;box-shadow:0 2px 4px rgba(0,0,0,.3)}
.main-nav{position:absolute;top:82px;left:488px;display:flex;gap:36px;font-family:"Roboto",sans-serif;font-weight:500;font-size:15.5px;color:var(--ink)}

/* hero */
.hero{position:absolute;left:0;top:120px;width:1200px;height:640px;background:linear-gradient(180deg,#6d6a58 0%,#8a7a5f 35%,#7b6a4e 70%,#5e523c 100%)}
.hero-curve{position:absolute;left:0;top:0}
.hero-title{position:absolute;left:0;width:1200px;top:318px;text-align:center;font-family:"Roboto",sans-serif;font-weight:900;font-size:48px;line-height:54px;color:var(--white);text-shadow:0 2px 6px rgba(0,0,0,.45)}
.hero-actions{position:absolute;top:468px;left:0;width:1200px;display:flex;justify-content:center;gap:14px}
.pill{height:40px;padding:0 30px;border-radius:20px;display:flex;align-items:center;font-family:"Roboto",sans-serif;font-weight:700;font-size:15px;color:var(--white)}
.pill-red{background:var(--red)}
.pill-dark{background:#222;border:2px solid #555}
.hero-dots{position:absolute;top:560px;left:0;width:1200px;display:flex;justify-content:center;gap:10px}
.hero-dots span{width:14px;height:14px;border-radius:50%;border:2px solid var(--white)}
.hero-dots span:first-child{background:var(--white)}

/* welcome */
.welcome-photo{position:absolute;left:130px;top:820px;width:330px;height:345px}
.welcome-ring{position:absolute;left:18px;top:25px;width:295px;height:295px;border-radius:50%;border:14px solid var(--red);background:var(--white)}
.welcome-img{position:absolute;left:44px;top:51px;width:243px;height:243px;border-radius:50%;background:radial-gradient(circle at 50% 45%,#9a7654 0%,#6b4e34 55%,#3d2f22 100%)}
.welcome-body{position:absolute;left:565px;top:880px;width:500px}
.welcome-body h2{font-family:"Roboto",sans-serif;font-weight:900;font-size:37px;color:var(--black);margin-bottom:28px}
.welcome-body h2 em{font-style:normal;color:var(--red)}
.welcome-body p{font-size:12.5px;line-height:25px;color:#333}
.btn-outline{display:inline-flex;margin-top:30px;height:34px;padding:0 18px;align-items:center;border:1.5px solid var(--ink);border-radius:17px;font-size:14px;color:var(--ink)}

/* vision / mission */
.purpose{position:absolute;left:0;top:1305px;width:1200px;height:523px;background:linear-gradient(101deg,var(--red-dark) 0%,var(--red) 30%,#b5161c 52.5%,#151515 52.6%,#262626 80%,#111 100%)}
.purpose-col{position:absolute;top:92px;width:480px;color:var(--white)}
.purpose-col h3{font-family:"Roboto",sans-serif;font-weight:700;font-size:27px;margin-bottom:26px}
.purpose-col ul{list-style:none}
.purpose-col li{display:flex;gap:16px;font-size:12.5px;font-weight:600;line-height:20px;margin-bottom:16px}
.paw{flex:none;width:18px;height:18px;margin-top:2px}
.btn-ghost{display:inline-flex;margin-top:20px;height:34px;padding:0 18px;align-items:center;border:1.5px solid var(--white);border-radius:17px;font-size:13px;font-weight:500;color:var(--white)}

/* how we do it */
.section-title{position:absolute;left:0;width:1200px;text-align:center;font-family:"Roboto",sans-serif;font-weight:500;font-size:34px;color:var(--black)}
.how-visual{position:absolute;left:427px;top:2040px;width:340px;height:355px;border-radius:50%;background:radial-gradient(circle at 50% 50%,#fff 0%,#fff 34%,#e63b3b 35%,#f3f3f3 60%,#fff 72%)}
.how-item{position:absolute;width:320px;display:flex;align-items:center;gap:22px;font-size:12.5px;line-height:26px;color:#333}
.how-left{left:90px;justify-content:flex-end;text-align:right}
.how-right{left:785px}
.how-badge{flex:none;width:88px;height:88px;border-radius:50%;border:6px solid var(--red);background:var(--white);display:flex;align-items:center;justify-content:center}

/* news */
.news-band{position:absolute;left:0;top:2490px;width:1200px;height:760px;background:var(--light)}
.news-card{position:absolute;top:2716px;width:292px;height:448px;background:var(--white);border-radius:6px;box-shadow:0 3px 10px rgba(0,0,0,.12);text-align:center}
.news-img{height:170px;border-radius:6px 6px 0 0}
.news-card h4{margin:28px 20px 0;font-size:17px;font-weight:400;line-height:26px;color:var(--navy)}
.news-date{margin-top:14px;font-size:16px;color:var(--red);display:flex;justify-content:center;align-items:center;gap:8px}
.news-card p{margin:22px 28px 0;font-size:11px;line-height:23px;color:#444}

/* footer */
.site-footer{position:absolute;left:0;top:3213px;width:1200px;height:553px;background:var(--black);color:var(--white)}
.foot-col{position:absolute;top:82px}
.foot-col h5{font-family:"Roboto",sans-serif;font-weight:700;font-size:24px;margin-bottom:28px}
.quick-links{list-style:none;font-size:13px;line-height:24px}
.quick-links li::before{content:"›";margin-right:12px}
.contact-list{list-style:none;font-size:12.5px;line-height:24px}
.contact-list li{display:flex;gap:14px;margin-bottom:12px}
.quote-form{display:grid;grid-template-columns:210px 210px;gap:12px 12px}
.field{height:40px;border:1px solid var(--white);font-size:11px;padding:12px 10px}
.field-wide{grid-column:1 / 3;height:56px}
.btn-submit{width:210px;height:40px;background:var(--red);font-family:"Roboto",sans-serif;font-weight:700;font-size:14px;display:flex;align-items:center;justify-content:center;margin-top:14px}
.foot-brand{position:absolute;left:133px;top:3640px;display:flex;align-items:center;gap:12px}
.foot-brand .brand-dot{width:64px;height:64px;background:var(--white)}
.foot-brand span{font-family:"Roboto",sans-serif;font-weight:700;font-size:20px;color:var(--white)}
.copyright{position:absolute;left:133px;top:3714px;font-size:12px;color:var(--white)}
.socials{position:absolute;left:970px;top:3706px;display:flex;gap:7px}
.socials span{width:20px;height:20px;border-radius:50%;border:1px solid var(--grey)}
</style>
</head>
<body>

<header class="site-header">
  <div class="brand"><span class="brand-dot"></span><span class="brand-name">Brindle Haven</span></div>
  <div class="callus">
    <svg width="26" height="26" viewBox="0 0 24 24"><path fill="#ec1f27" d="M6.6 10.8a15.1 15.1 0 0 0 6.6 6.6l2.2-2.2c.3-.3.7-.4 1-.2 1.1.4 2.3.6 3.6.6.6 0 1 .4 1 1V20c0 .6-.4 1-1 1A17 17 0 0 1 3 4c0-.6.4-1 1-1h3.5c.6 0 1 .4 1 1 0 1.3.2 2.5.6 3.6.1.3 0 .7-.2 1z"/></svg>
    <div><small>Call Us Today!</small><strong>555-014-2290</strong></div>
  </div>
  <div class="btn-donate-top">DONATE NOW</div>
  <nav class="main-nav"><span>HOME</span><span>ABOUT US</span><span>JOIN US</span><span>HELP US</span><span>FAQS</span><span>CONTACT US</span></nav>
</header>

<section class="hero" role="img" aria-label="Rescuers wading through flood water carrying a dog">
  <svg class="hero-curve" width="1200" height="640" viewBox="0 0 1200 640">
    <path d="M0 500 C 160 520 250 632 600 635 C 950 632 1040 520 1200 500 L1200 640 L0 640 Z" fill="#ffffff"/>
    <path d="M0 500 C 160 520 250 632 600 635 C 950 632 1040 520 1200 500" fill="none" stroke="#ec1f27" stroke-width="5"/>
  </svg>
  <h1 class="hero-title">BRINDLE HAVEN<br>NEW ZEALAND</h1>
  <div class="hero-actions"><span class="pill pill-red">DONATE NOW</span><span class="pill pill-dark">HELP FUNDRAISE</span></div>
  <div class="hero-dots"><span></span><span></span><span></span></div>
</section>

<section>
  <div class="welcome-photo">
    <div class="welcome-ring"></div>
    <div class="welcome-img" role="img" aria-label="Close portrait of a brindle rescue dog"></div>
  </div>
  <div class="welcome-body">
    <h2>Welcome to <em>Brindle Haven</em></h2>
    <p>Formed in 2018, following the devastating Tarawell flood the year prior that saw over 1,000 animals left behind in need of rescue, Brindle Haven New Zealand (Kaitiaki Rerenga) is a charity comprised of volunteers including veterinary and disaster response professionals, to ensure the needs of animals are better served in future emergencies. Though there is a primary focus on companion animals, Brindle Haven works to advocate for all animals</p>
    <span class="btn-outline">Read More</span>
  </div>
</section>

<section class="purpose" aria-label="Vision and mission">
  <div class="purpose-col" style="left:133px">
    <h3>Vision : Our hope</h3>
    <ul>
      <li><svg class="paw" viewBox="0 0 20 20"><g fill="#fff"><ellipse cx="10" cy="13.5" rx="4.5" ry="4"/><circle cx="4" cy="8" r="2"/><circle cx="8" cy="4.5" r="2"/><circle cx="12.5" cy="4.5" r="2"/><circle cx="16" cy="8" r="2"/></g></svg><span>An animal-inclusive and disaster resilient New Zealand.<br>Purpose: Why Brindle Haven New Zealand</span></li>
      <li><svg class="paw" viewBox="0 0 20 20"><g fill="#fff"><ellipse cx="10" cy="13.5" rx="4.5" ry="4"/><circle cx="4" cy="8" r="2"/><circle cx="8" cy="4.5" r="2"/><circle cx="12.5" cy="4.5" r="2"/><circle cx="16" cy="8" r="2"/></g></svg><span>To address the significant animal welfare emergency management capability gap</span></li>
      <li><svg class="paw" viewBox="0 0 20 20"><g fill="#fff"><ellipse cx="10" cy="13.5" rx="4.5" ry="4"/><circle cx="4" cy="8" r="2"/><circle cx="8" cy="4.5" r="2"/><circle cx="12.5" cy="4.5" r="2"/><circle cx="16" cy="8" r="2"/></g></svg><span>To protect disaster affected animals in partnership with the community</span></li>
      <li><svg class="paw" viewBox="0 0 20 20"><g fill="#fff"><ellipse cx="10" cy="13.5" rx="4.5" ry="4"/><circle cx="4" cy="8" r="2"/><circle cx="8" cy="4.5" r="2"/><circle cx="12.5" cy="4.5" r="2"/><circle cx="16" cy="8" r="2"/></g></svg><span>To provide local response to support animal evacuation, sheltering and reunification.</span></li>
    </ul>
    <span class="btn-ghost">READ MORE</span>
  </div>
  <div class="purpose-col" style="left:685px">
    <h3>Mission : What we do</h3>
    <ul>
      <li><svg class="paw" viewBox="0 0 20 20"><g fill="#fff"><ellipse cx="10" cy="13.5" rx="4.5" ry="4"/><circle cx="4" cy="8" r="2"/><circle cx="8" cy="4.5" r="2"/><circle cx="12.5" cy="4.5" r="2"/><circle cx="16" cy="8" r="2"/></g></svg><span>A. Promote animal-inclusive hazard mitigation, emergency preparedness and recovery</span></li>
      <li><svg class="paw" viewBox="0 0 20 20"><g fill="#fff"><ellipse cx="10" cy="13.5" rx="4.5" ry="4"/><circle cx="4" cy="8" r="2"/><circle cx="8" cy="4.5" r="2"/><circle cx="12.5" cy="4.5" r="2"/><circle cx="16" cy="8" r="2"/></g></svg><span>B. Develop and maintain a regional capability of animal emergency responders</span></li>
      <li><svg class="paw" viewBox="0 0 20 20"><g fill="#fff"><ellipse cx="10" cy="13.5" rx="4.5" ry="4"/><circle cx="4" cy="8" r="2"/><circle cx="8" cy="4.5" r="2"/><circle cx="12.5" cy="4.5" r="2"/><circle cx="16" cy="8" r="2"/></g></svg><span>C. Provide training and professional development in animal disaster management</span></li>
      <li><svg class="paw" viewBox="0 0 20 20"><g fill="#fff"><ellipse cx="10" cy="13.5" rx="4.5" ry="4"/><circle cx="4" cy="8" r="2"/><circle cx="8" cy="4.5" r="2"/><circle cx="12.5" cy="4.5" r="2"/><circle cx="16" cy="8" r="2"/></g></svg><span>D. Provide initial response to support to emergency services with the evacuation of animals and their temporary care</span></li>
    </ul>
    <span class="btn-ghost">READ MORE</span>
  </div>
</section>

<section aria-label="How we do it">
  <h2 class="section-title" style="top:1918px">HOW WE DO IT</h2>
  <div class="how-visual" role="img" aria-label="Small dog in sunglasses resting in a red and white life ring"></div>

  <div class="how-item how-left" style="top:2050px"><span>We are the leading voice<br>for all animals affected<br>by disaster</span><span class="how-badge"><svg class="paw" style="width:34px;height:34px" viewBox="0 0 20 20"><g fill="#ec1f27"><ellipse cx="10" cy="13.5" rx="4.5" ry="4"/><circle cx="4" cy="8" r="2"/><circle cx="8" cy="4.5" r="2"/><circle cx="12.5" cy="4.5" r="2"/><circle cx="16" cy="8" r="2"/></g></svg></span></div>
  <div class="how-item how-left" style="top:2172px"><span>We act to do the right<br>thing for the animals in a<br>disaster management</span><span class="how-badge"><svg class="paw" style="width:34px;height:34px" viewBox="0 0 20 20"><g fill="#ec1f27"><ellipse cx="10" cy="13.5" rx="4.5" ry="4"/><circle cx="4" cy="8" r="2"/><circle cx="8" cy="4.5" r="2"/><circle cx="12.5" cy="4.5" r="2"/><circle cx="16" cy="8" r="2"/></g></svg></span></div>
  <div class="how-item how-left" style="top:2296px"><span>We develop local capacity<br>to create animal inclusive<br>community resilience</span><span class="how-badge"><svg class="paw" style="width:34px;height:34px" viewBox="0 0 20 20"><g fill="#ec1f27"><ellipse cx="10" cy="13.5" rx="4.5" ry="4"/><circle cx="4" cy="8" r="2"/><circle cx="8" cy="4.5" r="2"/><circle cx="12.5" cy="4.5" r="2"/><circle cx="16" cy="8" r="2"/></g></svg></span></div>

  <div class="how-item how-right" style="top:2050px"><span class="how-badge"><svg class="paw" style="width:34px;height:34px" viewBox="0 0 20 20"><g fill="#ec1f27"><ellipse cx="10" cy="13.5" rx="4.5" ry="4"/><circle cx="4" cy="8" r="2"/><circle cx="8" cy="4.5" r="2"/><circle cx="12.5" cy="4.5" r="2"/><circle cx="16" cy="8" r="2"/></g></svg></span><span>We hold to account those with<br>responsibilities to protect<br>animals from disaster</span></div>
  <div class="how-item how-right" style="top:2172px"><span class="how-badge"><svg class="paw" style="width:34px;height:34px" viewBox="0 0 20 20"><g fill="#ec1f27"><ellipse cx="10" cy="13.5" rx="4.5" ry="4"/><circle cx="4" cy="8" r="2"/><circle cx="8" cy="4.5" r="2"/><circle cx="12.5" cy="4.5" r="2"/><circle cx="16" cy="8" r="2"/></g></svg></span><span>We inform our position and<br>activities using best practice<br>and scientific knowledge</span></div>
  <div class="how-item how-right" style="top:2296px"><span class="how-badge"><svg class="paw" style="width:34px;height:34px" viewBox="0 0 20 20"><g fill="#ec1f27"><ellipse cx="10" cy="13.5" rx="4.5" ry="4"/><circle cx="4" cy="8" r="2"/><circle cx="8" cy="4.5" r="2"/><circle cx="12.5" cy="4.5" r="2"/><circle cx="16" cy="8" r="2"/></g></svg></span><span>We do not advocate on non<br>disaster related animal welfare<br>issues</span></div>
</section>

<div class="news-band"></div>
<svg class="abs" style="left:0;top:2480px" width="1200" height="70" viewBox="0 0 1200 70"><path d="M0 0 H1200 V20 C1000 70 800 10 600 30 C400 50 200 70 0 40 Z" fill="#ffffff"/></svg>
<section aria-label="Latest news">
  <h2 class="section-title" style="top:2604px">LATEST NEWS</h2>
  <article class="news-card" style="left:133px"><div class="news-img" role="img" aria-label="Volunteer comforting a rescued animal among debris" style="background:linear-gradient(135deg,#8d8476,#5d5548)"></div><h4>Sed ut perspiciatis unde omnis iste natus</h4><div class="news-date"><svg width="13" height="13" viewBox="0 0 14 14"><rect x="1" y="2.5" width="12" height="10.5" fill="none" stroke="#ec1f27" stroke-width="1.6"/><path d="M1 6h12M4 1v3M10 1v3" stroke="#ec1f27" stroke-width="1.6"/></svg>Oct 01, 2018</div><p>Sed ut perspiciatis unde omnis iste natus error sit voluptatem accusantium doloque laudantium, totam</p></article>
  <article class="news-card" style="left:457px"><div class="news-img" role="img" aria-label="Group of volunteers standing together indoors" style="background:linear-gradient(135deg,#8a6a4e,#3e352e)"></div><h4>Sed ut perspiciatis unde omnis iste natus</h4><div class="news-date"><svg width="13" height="13" viewBox="0 0 14 14"><rect x="1" y="2.5" width="12" height="10.5" fill="none" stroke="#ec1f27" stroke-width="1.6"/><path d="M1 6h12M4 1v3M10 1v3" stroke="#ec1f27" stroke-width="1.6"/></svg>Oct 01, 2018</div><p>Sed ut perspiciatis unde omnis iste natus error sit voluptatem accusantium doloque laudantium, totam</p></article>
  <article class="news-card" style="left:781px"><div class="news-img" role="img" aria-label="Community gathering outside a building under blue sky" style="background:linear-gradient(180deg,#4f7fbf,#6d7a58 65%,#3d3a33)"></div><h4>Sed ut perspiciatis unde omnis iste natus</h4><div class="news-date"><svg width="13" height="13" viewBox="0 0 14 14"><rect x="1" y="2.5" width="12" height="10.5" fill="none" stroke="#ec1f27" stroke-width="1.6"/><path d="M1 6h12M4 1v3M10 1v3" stroke="#ec1f27" stroke-width="1.6"/></svg>Oct 01, 2018</div><p>Sed ut perspiciatis unde omnis iste natus error sit voluptatem accusantium doloque laudantium, totam</p></article>
</section>

<footer class="site-footer">
  <svg class="abs" style="left:0;top:-40px" width="1200" height="42" viewBox="0 0 1200 42"><path d="M0 42 V20 C300 0 450 40 700 22 C900 8 1050 0 1200 18 V42 Z" fill="#000000"/></svg>
  <div class="foot-col" style="left:133px">
    <h5>QUICK LINKS</h5>
    <ul class="quick-links"><li>Home</li><li>About Us</li><li>Join Us</li><li>Help Us</li><li>Faqs</li><li>Contact Us</li></ul>
  </div>
  <div class="foot-col" style="left:341px;width:260px">
    <h5>CONTACT US</h5>
    <ul class="contact-list">
      <li><svg width="14" height="18" viewBox="0 0 14 18" style="flex:none;margin-top:4px"><path d="M7 0a7 7 0 0 0-7 7c0 5 7 11 7 11s7-6 7-11a7 7 0 0 0-7-7zm0 9.5A2.5 2.5 0 1 1 7 4.5a2.5 2.5 0 0 1 0 5z" fill="#fff"/></svg><span>Brindle Haven New<br>Harbour Lane 42, Kelmont,<br>Westvale 6021</span></li>
      <li><svg width="14" height="14" viewBox="0 0 24 24" style="flex:none;margin-top:5px"><path fill="#fff" d="M6.6 10.8a15.1 15.1 0 0 0 6.6 6.6l2.2-2.2c.3-.3.7-.4 1-.2 1.1.4 2.3.6 3.6.6.6 0 1 .4 1 1V20c0 .6-.4 1-1 1A17 17 0 0 1 3 4c0-.6.4-1 1-1h3.5c.6 0 1 .4 1 1 0 1.3.2 2.5.6 3.6.1.3 0 .7-.2 1z"/></svg><span>Phone : 555-014-2290<br>Fax : 555-014-2291</span></li>
      <li><svg width="14" height="12" viewBox="0 0 14 12" style="flex:none;margin-top:6px"><rect width="14" height="12" fill="#fff"/><path d="M0 0l7 6 7-6" fill="none" stroke="#000" stroke-width="1.3"/></svg><span>Email : info@brindlehaven.nz</span></li>
    </ul>
  </div>
  <div class="foot-col" style="left:633px">
    <h5>GET A QUOTE</h5>
    <p style="font-size:12.5px;margin:-6px 0 24px">Alternatively You Can Fill In The Following Contact Form:</p>
    <div class="quote-form">
      <div class="field">Name</div><div class="field">E - Mail</div>
      <div class="field">Phone No</div><div class="field">Subject</div>
      <div class="field field-wide">Comments</div>
    </div>
    <div class="btn-submit">SUBMIT</div>
  </div>
</footer>
<div class="foot-brand"><span class="brand-dot"></span><span>Brindle Haven</span></div>
<div class="copyright">© 2018 Brindle Haven . All Rights Reserved.</div>
<div class="socials" aria-label="Social media links"><span></span><span></span><span></span><span></span></div>

</body>
</html>
```